To design a brand identity that is simple and creative with 'Corvane' as the brand name, I like modern simple fonts like helvetica neue, I want to print both sides of the card, I am open to dark front and white back, but the design needs to transfer well to letter heads and email signatures, I am looking for sophisticated and elegant, but open minded about clever and off the wall, I do not do 'boring' Corvane Ventures is the mother company for a small group, specialising in Management & consulting, Software development and construction, we have a high level of integrity, we are transparent and accountable for what we do. my images are provided as a guide only, Im not expecting them to be just copied, Im looking for a creator and passionate thinker, who will put life into their work.

Target Market(s)

usually business minded people who are looking for something different in me, such as leadership, confidence and focus with thinking that is per haps a little outside the box..

Industry/Entity Type

Construction

Requirements
Must have
• clean, minmalistic
Nice to have
• custom logo
Should not have
• boring, traditional

```html
<!DOCTYPE html>
<html lang="en">
<head>
<meta charset="utf-8">
<title>Corvane – Business Card</title>
<link rel="stylesheet" href="https://fonts.googleapis.com/css2?family=Inter:ital,wght@0,200;0,300;0,400;1,400&family=Dancing+Script&display=swap">
<style>
  :root {
    --stage: #2f2b29;
    --card-light: #ffffff;
    --card-light-shade: #e9e9ec;
    --card-dark: #3b3a3a;
    --card-dark-edge: #232323;
    --accent-red: #d8363d;
    --rule-soft: #e6b7b9;
    --name-red: #e2421f;
    --brand-orange: #e0683c;
    --ink: #1c1c1c;
    --ink-soft: #6a6a6a;
    --ghost: #e3e3e3;
    --back-word: #7d7d7d;
    --back-services: #d8d8d8;
    --label-light: #ffffff;
    --label-muted: #cfcfcf;
  }
  * { margin: 0; padding: 0; box-sizing: border-box; }
  html, body { width: 1000px; height: 1200px; overflow: hidden; }
  body {
    background: var(--stage);
    font-family: "Inter", "Helvetica Neue", Arial, sans-serif;
    position: relative;
  }
  .card {
    position: absolute;
    width: 740px;
    height: 455px;
    box-shadow: 0 4px 10px rgba(0,0,0,.45);
    overflow: hidden;
  }
  .card-front {
    left: 135px; top: 75px;
    background: linear-gradient(160deg, var(--card-light) 40%, var(--card-light-shade) 100%);
  }
  .card-back {
    left: 117px; top: 652px;
    background: radial-gradient(ellipse at 50% 50%, var(--card-dark) 0%, var(--card-dark-edge) 100%);
  }
  .holder-name {
    position: absolute; left: 45px; top: 56px;
    font-size: 30px; font-weight: 400; color: var(--name-red);
  }
  .holder-role {
    position: absolute; left: 47px; top: 95px;
    font-size: 18px; font-style: italic; color: var(--ink-soft);
  }
  .ghost-word {
    position: absolute; left: 43px; top: 108px;
    font-size: 64px; font-weight: 200; color: var(--ghost); letter-spacing: -1px;
    line-height: 1;
  }
  .contact {
    position: absolute; display: flex; align-items: center; gap: 9px;
    font-size: 17px; color: var(--ink);
  }
  .contact svg { width: 18px; height: 18px; flex: none; }
  .contact-phone { right: 46px; top: 60px; }
  .contact-mail { right: 46px; top: 93px; }
  .contact-post { left: 45px; top: 296px; }
  .contact-web { left: 45px; top: 327px; }
  .brand-lockup {
    position: absolute; right: 45px; top: 244px;
    display: flex; align-items: center; gap: 22px;
  }
  .brand-dot { width: 54px; height: 54px; border-radius: 50%; background: var(--brand-orange); }
  .brand-word {
    font-size: 62px; font-weight: 200; color: var(--brand-orange); line-height: 1;
  }
  .tagline {
    position: absolute; right: 45px; top: 322px;
    font-family: "Dancing Script", cursive; font-size: 21px; color: var(--ink-soft);
  }
  .rule {
    position: absolute; left: 45px; top: 372px; width: 292px; height: 8px;
    border-top: 4px solid var(--accent-red);
    border-bottom: 2px solid var(--rule-soft);
  }
  .services {
    position: absolute; display: flex; align-items: center; gap: 10px;
    font-size: 16px; letter-spacing: 1px; white-space: nowrap;
  }
  .services .sep { width: 5px; height: 5px; border-radius: 50%; background: var(--accent-red); }
  .card-front .services { right: 45px; top: 366px; color: var(--ink); }
  .card-back .services { left: 0; right: 0; top: 326px; justify-content: center; color: var(--back-services); }
  .back-mark {
    position: absolute; left: 315px; top: 115px;
    width: 110px; height: 110px; border-radius: 50%;
    background: var(--brand-orange);
  }
  .back-word {
    position: absolute; left: 0; right: 0; top: 232px; text-align: center;
    font-size: 66px; font-weight: 200; color: var(--back-word); letter-spacing: -1px;
    line-height: 1;
  }
  .side-label { position: absolute; font-size: 19px; }
  .label-front { left: 811px; top: 570px; color: var(--label-light); }
  .label-back { left: 117px; top: 1144px; color: var(--label-muted); }
</style>
</head>
<body>
  <section class="card card-front" aria-label="Card front">
    <div class="holder-name">Mara Quill</div>
    <div class="holder-role">client ambassador</div>
    <div class="ghost-word" aria-hidden="true">corvane</div>

    <div class="contact contact-phone">
      <span>+61 0400 555 192</span>
      <svg viewBox="0 0 24 24" aria-hidden="true"><path fill="#d8363d" d="M6.6 2.5l3 3.5-2 2.3c1.2 3 3.4 5.3 6.3 6.6l2.3-2 3.5 3-1.8 3.4C11 19 5 13 3.2 4.4z"/></svg>
    </div>
    <div class="contact contact-mail">
      <span>info@corvane.com.au</span>
      <svg viewBox="0 0 24 24" aria-hidden="true"><rect x="2" y="5" width="20" height="14" fill="#d8363d"/><path d="M2 5l10 8 10-8" fill="none" stroke="#fff" stroke-width="1.6"/></svg>
    </div>

    <div class="brand-lockup">
      <div class="brand-dot"></div>
      <div class="brand-word">corvane.</div>
    </div>
    <div class="tagline">..shaping what comes next.</div>

    <div class="contact contact-post">
      <svg viewBox="0 0 24 24" aria-hidden="true"><path fill="#d8363d" d="M12 1.5a7 7 0 0 0-7 7c0 5.2 7 14 7 14s7-8.8 7-14a7 7 0 0 0-7-7zm0 9.6a2.6 2.6 0 1 1 0-5.2 2.6 2.6 0 0 1 0 5.2z"/></svg>
      <span>po box 512 perth 6010</span>
    </div>
    <div class="contact contact-web">
      <svg viewBox="0 0 24 24" aria-hidden="true"><g fill="none" stroke="#d8363d" stroke-width="2"><circle cx="12" cy="12" r="9.5"/><path d="M2.5 12h19"/><ellipse cx="12" cy="12" rx="4.2" ry="9.5"/></g></svg>
      <span>www.corvane.com.au</span>
    </div>

    <div class="rule"></div>
    <div class="services">
      <span>management</span><span class="sep"></span><span>software</span><span class="sep"></span><span>construction</span>
    </div>
  </section>
  <div class="side-label label-front">Front</div>

  <section class="card card-back" aria-label="Card back">
    <div class="back-mark"></div>
    <div class="back-word">corvane</div>
    <div class="services">
      <span>management</span><span class="sep"></span><span>software</span><span class="sep"></span><span>construction</span>
    </div>
  </section>
  <div class="side-label label-back">Back</div>
</body>
</html>
```